I want a website to be designed for our new company, it's an import and export company for variety of things.

please see the attached Logo for our company and the Images for our different sections for our busienss

Target Market(s)

multiple

Coding

Coded - Design and coding required

Number of Pages Required

5+ page

Font styles to use
Sans Serif

Colors

Designer to choose colors to be used in the design.

Requirements
Must have
• KVR GLOBALINKS
• KVR globalinks Trading & Contracting provides various services. The Company offers infrastructure construction, oil, enegy and gas services, agricultural projects, real estate development, travel and tourism, and food processing and trading.
• Civil contracting for infrastructure, residential and heavy projects. Through its main subsidiaries; distribution of general food products, construction chemicals including corrosion inhibitors and electrical machinery; provides catering and travel agency services; ownership and operation of a school; offers human sources services including manpower supply.
• Drilling and Gold Mines Used Machinery, All Kinds of Construction Machinery, Drilling Machines are manufactured and sold.
Nice to have
• good designa and beautiful colours, it has too look professional

```html
<!DOCTYPE html>
<html lang="en">
<head>
<meta charset="utf-8">
<title>KVR GLOBALINKS</title>
<link rel="stylesheet" href="https://fonts.googleapis.com/css2?family=Cinzel:wght@400;700&family=Montserrat:ital,wght@0,400;0,500;0,600;0,700;1,400&display=swap">
<style>
:root{
  --gold:#8f6c2f;
  --gold-band:#8d6b30;
  --gold-light:#d9c9a4;
  --ink:#3b3b3b;
  --muted:#8a8a8a;
  --white:#ffffff;
  --dark:#1b1618;
  --hero-a:#2b5868;
  --hero-b:#0f2530;
  --card:#efefef;
}
*{margin:0;padding:0;box-sizing:border-box}
html,body{width:1200px;height:4338px;overflow:hidden}
body{position:relative;background:var(--white);font-family:"Montserrat",sans-serif;color:var(--ink)}
.abs{position:absolute}
.serif{font-family:"Cinzel",serif}

/* header / hero */
.hero{left:0;top:0;width:1200px;height:840px;background:radial-gradient(ellipse at 50% 35%,var(--hero-a) 0%,#1c3f4d 45%,var(--hero-b) 100%)}
.hero-curve{left:0;top:690px;width:1200px;height:150px}
.brand{left:143px;top:60px;display:flex;align-items:center;gap:10px;font-family:"Cinzel",serif;font-weight:400;font-size:22px;letter-spacing:2px;color:var(--white)}
.brand-dot{width:14px;height:14px;border-radius:50%;background:var(--gold-light)}
.nav{top:68px;font-size:14px;font-weight:500;color:var(--white);transform:translateX(-50%);white-space:nowrap}
.nav.active::after{content:"";position:absolute;left:0;right:0;top:28px;height:2px;background:var(--gold)}
.search{left:1040px;top:70px;width:16px;height:16px}
.hero-title{left:0;width:1200px;top:206px;text-align:center;font-family:"Cinzel",serif;font-size:60px;color:var(--white);letter-spacing:1px}
.hero-sub{left:0;width:1200px;top:305px;text-align:center;font-size:17px;color:var(--white)}
.btn{display:flex;align-items:center;justify-content:center;gap:8px;background:var(--gold);color:var(--white);font-weight:600;letter-spacing:.5px;text-transform:uppercase}
.btn svg{width:14px;height:14px}
.hero-btn{left:510px;top:370px;width:178px;height:47px;font-size:15px}
.dots{left:0;width:1200px;top:725px;display:flex;justify-content:center;gap:7px}
.dots span{width:9px;height:9px;border-radius:50%;background:var(--white)}
.dots span.on{background:var(--gold)}

/* section headings */
.ornament{width:76px;height:22px;background:linear-gradient(90deg,#c8b48a,#a8906a,#c8b48a);border-radius:11px 11px 3px 3px;opacity:.8}
.h2{font-family:"Cinzel",serif;font-size:44px;line-height:50px;color:#4a4a4a;letter-spacing:1px}
.h2 .gold{color:var(--gold);display:block}
.copy{font-size:13.5px;line-height:31px;color:var(--muted)}
.btn-sm{height:42px;font-size:14px}

.photo-round{border-radius:50%;border:3px solid #c8c8c8;padding:12px;background:var(--white)}
.photo-round div{width:100%;height:100%;border-radius:50%}

/* tiles */
.tiles{left:0;top:1385px;width:1200px;height:365px;display:flex}
.tile{position:relative;width:300px;height:365px}
.tile p{position:absolute;left:0;right:0;bottom:32px;text-align:center;color:var(--white);font-weight:600;font-size:17px;line-height:26px;letter-spacing:.5px}
.tile-arrow{position:absolute;top:167px;width:32px;height:32px}

/* reviews */
.band{left:0;top:2410px;width:1200px;height:590px;background:var(--gold-band)}
.band-title{left:0;width:1200px;top:2530px;text-align:center;font-family:"Cinzel",serif;font-size:44px;color:var(--white);letter-spacing:1px}
.avatar{width:66px;height:66px;border-radius:50%;border:3px solid var(--white);background:linear-gradient(160deg,#d9c2a8,#8b7362)}
.review{width:215px;color:var(--white)}
.review q{display:block;quotes:none;font-style:italic;font-size:12.5px;line-height:22px}
.review q b{font-family:"Cinzel",serif;font-style:normal;font-size:20px;margin-right:6px}
.review .name{margin-top:28px;font-size:9.5px;font-weight:700;text-transform:uppercase}
.review .role{font-size:9.5px;font-weight:600;margin-top:3px}
.review .stars{margin-top:18px;font-size:18px;letter-spacing:4px;color:#f3c623}
.ring-arrow{width:34px;height:34px}

/* blog */
.blog-title{left:0;width:1200px;top:3116px;text-align:center;font-family:"Cinzel",serif;font-size:44px;color:#4a4a4a;letter-spacing:1px}
.card{top:3225px;width:293px;height:360px;background:var(--card);padding:10px}
.card .img{position:relative;height:160px}
.card .date{position:absolute;right:0;bottom:0;background:var(--gold);color:var(--white);font-size:13px;font-weight:700;padding:6px 14px 5px}
.card h3{margin:24px 0 0 15px;font-size:15px;font-weight:600;color:#333}
.card p{margin:10px 15px 0;font-size:11.5px;line-height:21px;color:var(--muted)}
.card a{display:block;margin:18px 0 0 15px;font-size:13px;font-weight:700;color:var(--gold);text-decoration:none}

/* footer */
.skyline{left:0;top:3610px;width:1200px;height:250px;background:linear-gradient(180deg,#ffffff 0%,#bdb9ba 30%,#2a2426 75%,var(--dark) 100%)}
.footer{left:0;top:3854px;width:1200px;height:484px;background:var(--dark)}
.footer-brand{left:0;width:1200px;top:3960px;display:flex;justify-content:center;align-items:center;gap:12px;font-family:"Cinzel",serif;font-size:26px;letter-spacing:3px;color:var(--white)}
.rule{left:143px;width:914px;height:1px;background:#3f3a3c}
.fnav{left:143px;width:914px;top:4120px;height:36px;display:flex;justify-content:center;align-items:center}
.fnav span{font-size:14px;font-weight:500;color:var(--white);padding:0 27px;border-left:1px solid #4a4446;line-height:36px}
.fnav span:first-child{border-left:none}
.social{top:4211px;width:34px;height:34px;border-radius:50%;background:var(--white)}
.copyright{left:0;width:1200px;top:4275px;text-align:center;font-size:12px;color:var(--white)}
</style>
</head>
<body>

<!-- hero -->
<div class="abs hero" role="img" aria-label="Team of business people standing before a globe and world map"></div>
<svg class="abs hero-curve" viewBox="0 0 1200 150" preserveAspectRatio="none">
  <path d="M0,143 C170,0 430,0 600,143 C770,0 1030,0 1200,143 L1200,150 L0,150 Z" fill="#ffffff"/>
</svg>

<div class="abs brand"><span class="brand-dot"></span>KVR GLOBALINKS</div>

<span class="abs nav active" style="left:520px">HOME</span>
<span class="abs nav" style="left:606px">ABOUT US</span>
<span class="abs nav" style="left:705px">SERVICES</span>
<span class="abs nav" style="left:808px">PRODUCTS</span>
<span class="abs nav" style="left:897px">NEWS</span>
<span class="abs nav" style="left:981px">CONTACT</span>
<svg class="abs search" viewBox="0 0 16 16"><circle cx="6.5" cy="6.5" r="4.8" fill="none" stroke="#fff" stroke-width="2"/><line x1="10" y1="10" x2="14.5" y2="14.5" stroke="#fff" stroke-width="2.4" stroke-linecap="round"/></svg>

<h1 class="abs hero-title">KVR GLOBALINKS</h1>
<p class="abs hero-sub">Lorem ipsum dolor sit amonsectetur adipiscing elito eiusmod tempor</p>
<div class="abs btn hero-btn">Get Started
  <svg viewBox="0 0 14 14"><circle cx="7" cy="7" r="7" fill="#fff"/><path d="M5,4 L8.5,7 L5,10" fill="none" stroke="#8f6c2f" stroke-width="2"/></svg>
</div>
<div class="abs dots"><span></span><span></span><span class="on"></span><span></span><span></span></div>

<!-- welcome -->
<div class="abs ornament" role="img" aria-label="Jewelled crest ornament" style="left:145px;top:880px"></div>
<h2 class="abs h2" style="left:145px;top:922px">Welcome to<span class="gold">KVR GLOBALINKS</span></h2>
<p class="abs copy" style="left:145px;top:1042px;width:460px">Lorem ipsum dolor sit amet, consectetur adipiscing elit, sed do eiusmod tempor incididunt ut labore et dolore magna aliqua. Quis ipsum suspendisse ultriceorem ipsum dolor sit consectetur adipiscing elit, sed do eiusmod tempor incididunt ut labore et dolore magna aliquis ipsum suspendisse</p>
<div class="abs btn btn-sm" style="left:145px;top:1232px;width:146px">Read More
  <svg viewBox="0 0 14 14"><circle cx="7" cy="7" r="7" fill="#fff"/><path d="M5,4 L8.5,7 L5,10" fill="none" stroke="#8f6c2f" stroke-width="2"/></svg>
</div>
<div class="abs photo-round" style="left:653px;top:875px;width:404px;height:404px">
  <div role="img" aria-label="Hands typing on a laptop showing business charts" style="background:radial-gradient(circle at 50% 40%,#6f7a80,#2b3034 55%,#c9ccd0 100%)"></div>
</div>

<!-- service tiles -->
<div class="abs tiles">
  <div class="tile" role="img" aria-label="Engineer in hard hat reviewing plans at sunset" style="background:linear-gradient(180deg,#7a4a10,#c07a20 40%,#2a1a0c)">
    <svg class="tile-arrow" style="left:24px" viewBox="0 0 32 32"><circle cx="16" cy="16" r="14" fill="none" stroke="#fff" stroke-width="2"/><path d="M23,16 H10 M15,10 L9,16 L15,22" fill="none" stroke="#fff" stroke-width="2"/></svg>
    <p>INFRASTRUCTURE<br>CONSTRUCTION</p>
  </div>
  <div class="tile" role="img" aria-label="Offshore oil rig at sea" style="background:linear-gradient(180deg,#6c7b7c,#3c5050 55%,#233233)"><p>OIL, ENEGY &amp; GAS<br>SERVICES</p></div>
  <div class="tile" role="img" aria-label="Assortment of fresh food and bottled produce" style="background:linear-gradient(180deg,#e6e1d5,#b79a62 55%,#5b4a2a)"><p>AGRICULTURAL<br>PROJECTS</p></div>
  <div class="tile" role="img" aria-label="Looking up at high-rise buildings" style="background:linear-gradient(160deg,#3e4350,#9a9ca2 50%,#565a62)">
    <svg class="tile-arrow" style="right:24px" viewBox="0 0 32 32"><circle cx="16" cy="16" r="14" fill="none" stroke="#fff" stroke-width="2"/><path d="M9,16 H22 M17,10 L23,16 L17,22" fill="none" stroke="#fff" stroke-width="2"/></svg>
    <p>REAL ESTATE<br>DEVELOPMENT</p>
  </div>
</div>

<!-- manufacturing -->
<div class="abs" role="img" aria-label="Line drawing of cranes and city buildings" style="left:180px;top:2120px;width:900px;height:290px;background:linear-gradient(180deg,#ffffff 0%,#f1f1f1 100%)"></div>
<div class="abs photo-round" style="left:145px;top:1860px;width:404px;height:404px">
  <div role="img" aria-label="Yellow drilling machine in a snowy forest" style="background:linear-gradient(135deg,#9ab0c4,#3f5668 50%,#e0a020 75%,#2f4558)"></div>
</div>
<div class="abs ornament" role="img" aria-label="Jewelled crest ornament" style="left:603px;top:1865px"></div>
<h2 class="abs h2" style="left:603px;top:1908px">Manufacturing<span class="gold">Drilling Machines</span></h2>
<p class="abs copy" style="left:603px;top:2027px;width:470px">Lorem ipsum dolor sit amet, consectetur adipiscing elit, sed do eiusmod tempor incididunt ut labore et dolore magna aliqua. Quis ipsum suspendisse ultriceorem ipsum dolor sit consectetur adipiscing elit, sed do eiusmod tempor incididunt ut labore et dolore magna aliquis ipsum suspendisse</p>
<div class="abs btn btn-sm" style="left:603px;top:2218px;width:148px">Read More
  <svg viewBox="0 0 14 14"><circle cx="7" cy="7" r="7" fill="#fff"/><path d="M5,4 L8.5,7 L5,10" fill="none" stroke="#8f6c2f" stroke-width="2"/></svg>
</div>

<!-- reviews -->
<div class="abs band"></div>
<svg class="abs" style="left:0;top:2900px" width="1200" height="100" viewBox="0 0 1200 100" preserveAspectRatio="none">
  <path d="M0,96 C170,-30 430,-30 600,96 C770,-30 1030,-30 1200,96 L1200,100 L0,100 Z" fill="#ffffff"/>
</svg>
<div class="abs ornament" role="img" aria-label="Jewelled crest ornament" style="left:562px;top:2490px"></div>
<h2 class="abs band-title">Customer Reviews</h2>

<svg class="abs ring-arrow" style="left:65px;top:2701px" viewBox="0 0 34 34"><circle cx="17" cy="17" r="15" fill="none" stroke="#fff" stroke-width="1.5"/><path d="M19,11 L13,17 L19,23" fill="none" stroke="#fff" stroke-width="1.5"/></svg>
<svg class="abs ring-arrow" style="left:1097px;top:2701px" viewBox="0 0 34 34"><circle cx="17" cy="17" r="15" fill="none" stroke="#fff" stroke-width="1.5"/><path d="M15,11 L21,17 L15,23" fill="none" stroke="#fff" stroke-width="1.5"/></svg>

<div class="abs avatar" role="img" aria-label="Reviewer portrait" style="left:130px;top:2627px"></div>
<div class="abs review" style="left:217px;top:2656px">
  <q><b>"</b>At vero eos et accusamus et iustodio dignissimos ducimus qui blanditiipraesnt ium</q>
  <div class="name">Marisa Dalton</div>
  <div class="role">Financial Services Professional</div>
  <div class="stars">★★★★☆</div>
</div>
<div class="abs avatar" role="img" aria-label="Reviewer portrait" style="left:457px;top:2627px"></div>
<div class="abs review" style="left:544px;top:2656px">
  <q><b>"</b>At vero eos et accusamus et iustodio dignissimos ducimus qui blanditiipraesnt ium</q>
  <div class="name">Teodor L. Vance</div>
  <div class="role">National Urban Fellow at the Riverside</div>
  <div class="stars">★★★★☆</div>
</div>
<div class="abs avatar" role="img" aria-label="Reviewer portrait" style="left:780px;top:2627px"></div>
<div class="abs review" style="left:867px;top:2656px;width:240px">
  <q><b>"</b>At vero eos et accusamus et iustodio dignissimos ducimus qui blanditiipraesnt ium</q>
  <div class="name">Ruth Okafor</div>
  <div class="role">Creative Strategist | Entrepreneur &amp; Upcoming</div>
  <div class="stars">★★★★☆</div>
</div>

<!-- blog -->
<div class="abs ornament" role="img" aria-label="Jewelled crest ornament" style="left:562px;top:3078px"></div>
<h2 class="abs blog-title">Blog Posts</h2>

<article class="abs card" style="left:141px">
  <div class="img" role="img" aria-label="Offshore platform at dusk" style="background:linear-gradient(180deg,#5a7fb8,#d38a6c 55%,#2c4a7a)"><span class="date">JAN 2019</span></div>
  <h3>LOREM IPSUM DOLORSME</h3>
  <p>Lorem ipsum dolor sit amet, consectetur adipiscing elit, sed do eiusmod tempor incididunt ut labore et dolore magna</p>
  <a>READ MORE</a>
</article>
<article class="abs card" style="left:454px">
  <div class="img" role="img" aria-label="Aerial view of a large building complex" style="background:linear-gradient(180deg,#6f7a70,#a9aca4 55%,#5a6458)"><span class="date">JAN 2019</span></div>
  <h3>LOREM IPSUM DOLORSME</h3>
  <p>Lorem ipsum dolor sit amet, consectetur adipiscing elit, sed do eiusmod tempor incididunt ut labore et dolore magna</p>
  <a>READ MORE</a>
</article>
<article class="abs card" style="left:766px">
  <div class="img" role="img" aria-label="Trading chart with rising arrow" style="background:linear-gradient(135deg,#1e1e1e,#4a4a4a 50%,#d98a20 52%,#2a2a2a)"><span class="date">JAN 2019</span></div>
  <h3>LOREM IPSUM DOLORSME</h3>
  <p>Lorem ipsum dolor sit amet, consectetur adipiscing elit, sed do eiusmod tempor incididunt ut labore et dolore magna</p>
  <a>READ MORE</a>
</article>

<!-- footer -->
<div class="abs skyline" role="img" aria-label="Silhouette of oil pumps, refinery and workers"></div>
<div class="abs footer"></div>
<div class="abs footer-brand"><span class="brand-dot"></span>KVR GLOBALINKS</div>
<div class="abs rule" style="top:4101px"></div>
<nav class="abs fnav"><span>HOME</span><span>ABOUT US</span><span>SERVICES</span><span>PRODUCTS</span><span>NEWS</span><span>CONTACT</span></nav>
<div class="abs rule" style="top:4174px"></div>
<div class="abs social" style="left:538px"></div>
<div class="abs social" style="left:583px"></div>
<div class="abs social" style="left:628px"></div>
<p class="abs copyright">Copyrights © 2020 KVR GLOBALINKS All Rights Reserved. &nbsp;|&nbsp; Privacy policy</p>

</body>
</html>
```